Landscape design build company door flyer

I would like this flyer to convey a high-level of professionalism for a company that is excellent with communication with their clients as well as a company that does incredible installations

Went on vacation/holiday

```html
<!DOCTYPE html>
<html lang="en">
<head>
<meta charset="utf-8">
<title>Cedarline Builders – Outdoor Living Spaces</title>
<link href="https://fonts.googleapis.com/css2?family=Poppins:wght@400;500;600;700&family=Roboto+Condensed:wght@600;700&display=swap" rel="stylesheet">
<style>
  :root {
    --orange: #ef7d1a;
    --navy: #1c3346;
    --ink: #1d1d1d;
    --paper: #f0f0f0;
    --panel: #e6e6e6;
    --stage: #e4e4e4;
    --white: #ffffff;
  }
  * { margin: 0; padding: 0; box-sizing: border-box; }
  html, body { width: 1200px; height: 1029px; overflow: hidden; }
  body {
    background: var(--stage);
    font-family: "Poppins", sans-serif;
    color: var(--ink);
    position: relative;
  }
  .flyer {
    position: absolute;
    left: 215px; top: 20px;
    width: 769px; height: 990px;
    background: var(--paper);
    overflow: hidden;
  }
  .hero-photo {
    position: absolute; left: 0; top: 0;
    width: 769px; height: 538px;
    background: linear-gradient(160deg, #8c9ea6 0%, #7f9096 30%, #2f4a33 55%, #1f3a26 70%, #4f8a3a 88%, #3f7a2e 100%);
  }
  .brand-panel {
    position: absolute; left: 0; top: 0;
    width: 402px; height: 168px;
    background: var(--panel);
    clip-path: polygon(0 0, 402px 0, 322px 168px, 0 168px);
  }
  .brand-mark {
    position: absolute; left: 141px; top: 26px;
    width: 56px; height: 56px;
    border-radius: 50%;
    background: var(--orange);
  }
  .brand-name {
    position: absolute; left: 0; width: 336px; top: 96px;
    text-align: center;
    font-size: 19px; font-weight: 600; letter-spacing: 0.5px;
    color: var(--orange);
  }
  .brand-tagline {
    position: absolute; left: 0; width: 336px; top: 125px;
    text-align: center;
    font-size: 9px; font-weight: 500;
    color: var(--navy);
  }
  .gallery-photo {
    position: absolute; top: 413px;
    width: 204px; height: 204px;
    border-radius: 50%;
    border: 6px solid var(--white);
  }
  .gallery-photo.deck { left: 45px; background: linear-gradient(180deg, #6d9fd0 0%, #4f7a3e 40%, #a44f24 60%, #7a3315 100%); }
  .gallery-photo.pavilion { left: 284px; background: linear-gradient(180deg, #8f9ba4 0%, #b07a44 35%, #4f5a52 65%, #6f9a3e 100%); }
  .gallery-photo.steps { left: 521px; background: linear-gradient(180deg, #3c4a2c 0%, #6a4a30 22%, #6e7372 45%, #4d5252 100%); }
  .section-title {
    position: absolute; top: 660px;
    font-size: 24px; font-weight: 600;
    color: var(--navy);
  }
  .section-title .accent { color: var(--orange); }
  .about-title { left: 34px; }
  .services-title { left: 454px; }
  .about-text {
    position: absolute; left: 34px; top: 706px; width: 326px;
    font-size: 12.6px; line-height: 14.7px;
    text-align: justify;
  }
  .service-areas {
    position: absolute; left: 34px; top: 866px; width: 326px;
    font-size: 12.8px; line-height: 16px; font-weight: 500;
    text-align: justify;
  }
  .column-rule {
    position: absolute; left: 402px; top: 653px;
    width: 1px; height: 242px;
    background: #dcdcdc;
  }
  .service-list {
    position: absolute; left: 454px; top: 696px;
    list-style: none;
  }
  .service-list li {
    display: flex; align-items: center;
    height: 25.7px;
    font-size: 16.5px; font-weight: 500;
  }
  .service-list svg { width: 16px; height: 16px; margin-right: 18px; flex: none; }
  .contact-heading {
    position: absolute; left: 34px; top: 924px;
    font-size: 27px; font-weight: 700; letter-spacing: 1.5px;
    color: var(--orange);
  }
  .contact-links {
    position: absolute; left: 34px; top: 953px;
    display: flex; gap: 30px;
    font-family: "Roboto Condensed", sans-serif;
    font-size: 12px; font-weight: 700;
    color: var(--navy);
  }
  .contact-links span { display: flex; align-items: center; gap: 5px; }
  .contact-links svg { width: 11px; height: 11px; }
  .phone-bar {
    position: absolute; left: 399px; top: 918px;
    width: 370px; height: 55px;
    background: var(--navy);
    display: flex; align-items: center;
  }
  .phone-icon {
    margin-left: 32px; width: 27px; height: 33px;
    background: var(--orange);
    display: flex; align-items: center; justify-content: center;
  }
  .phone-number {
    margin-left: 12px;
    font-family: "Roboto Condensed", sans-serif;
    font-size: 40px; font-weight: 700; letter-spacing: 0.5px;
    color: var(--white);
  }
</style>
</head>
<body>
<main class="flyer">
  <div class="hero-photo" role="img" aria-label="Photo of a two-level grey composite deck with cedar railings and stairs behind a house, evergreen trees and lawn"></div>

  <header class="brand-panel">
    <div class="brand-mark"></div>
    <div class="brand-name">CEDARLINE BUILDERS</div>
    <div class="brand-tagline">OUTDOOR LIVING SPACES</div>
  </header>

  <div class="gallery-photo deck" role="img" aria-label="Photo of a stained wood deck with patio chairs and a pergola"></div>
  <div class="gallery-photo pavilion" role="img" aria-label="Photo of a covered outdoor kitchen with stone counters under a cedar roof"></div>
  <div class="gallery-photo steps" role="img" aria-label="Photo of grey concrete block steps set into a retaining wall"></div>

  <h2 class="section-title about-title"><span class="accent">ABOUT</span> US</h2>
  <p class="about-text">Discover the endless possibilities for your outdoor space with The Cedarline Builders Team. Our team of skilled artisans is dedicated to turning your outdoor space into a breathtaking oasis that you’ll love coming home to. Whether it’s a cozy patio for intimate gatherings, a sprawling deck to host memorable parties, or a custom paver driveway that adds instant curb appeal, our high-quality craftsmanship ensures stunning results that exceed your expectations.</p>
  <p class="service-areas">Our service areas include Bellevue, Issaquah, Kirkland, Redmond, Sammamish.</p>

  <div class="column-rule"></div>

  <h2 class="section-title services-title"><span class="accent">OUR</span> SERVICES</h2>
  <ul class="service-list">
    <li><svg viewBox="0 0 16 16"><circle cx="8" cy="8" r="8" fill="#ef7d1a"/><path d="M4.5 8.2l2.3 2.3 4.7-4.9" fill="none" stroke="#fff" stroke-width="1.8"/></svg>Paver Patios</li>
    <li><svg viewBox="0 0 16 16"><circle cx="8" cy="8" r="8" fill="#ef7d1a"/><path d="M4.5 8.2l2.3 2.3 4.7-4.9" fill="none" stroke="#fff" stroke-width="1.8"/></svg>Paver Driveways</li>
    <li><svg viewBox="0 0 16 16"><circle cx="8" cy="8" r="8" fill="#ef7d1a"/><path d="M4.5 8.2l2.3 2.3 4.7-4.9" fill="none" stroke="#fff" stroke-width="1.8"/></svg>Retaining Walls</li>
    <li><svg viewBox="0 0 16 16"><circle cx="8" cy="8" r="8" fill="#ef7d1a"/><path d="M4.5 8.2l2.3 2.3 4.7-4.9" fill="none" stroke="#fff" stroke-width="1.8"/></svg>Decks &amp; Railings</li>
    <li><svg viewBox="0 0 16 16"><circle cx="8" cy="8" r="8" fill="#ef7d1a"/><path d="M4.5 8.2l2.3 2.3 4.7-4.9" fill="none" stroke="#fff" stroke-width="1.8"/></svg>Pools</li>
    <li><svg viewBox="0 0 16 16"><circle cx="8" cy="8" r="8" fill="#ef7d1a"/><path d="M4.5 8.2l2.3 2.3 4.7-4.9" fill="none" stroke="#fff" stroke-width="1.8"/></svg>Outdoor Lighting</li>
    <li><svg viewBox="0 0 16 16"><circle cx="8" cy="8" r="8" fill="#ef7d1a"/><path d="M4.5 8.2l2.3 2.3 4.7-4.9" fill="none" stroke="#fff" stroke-width="1.8"/></svg>Firepits &amp; Fireplaces</li>
  </ul>

  <h2 class="contact-heading">CONTACT US TODAY!</h2>
  <div class="contact-links">
    <span><svg viewBox="0 0 12 12"><rect x="0.5" y="2" width="11" height="8" fill="#ef7d1a"/><path d="M0.5 2l5.5 4.5 5.5-4.5" fill="none" stroke="#fff" stroke-width="1"/></svg>www.cedarlinebuilders.com</span>
    <span><svg viewBox="0 0 12 12"><circle cx="6" cy="6" r="5.3" fill="none" stroke="#ef7d1a" stroke-width="1"/><ellipse cx="6" cy="6" rx="2.3" ry="5.3" fill="none" stroke="#ef7d1a" stroke-width="1"/><path d="M0.7 6h10.6" stroke="#ef7d1a" stroke-width="1"/></svg>hello@cedarlinebuilders.com</span>
  </div>

  <div class="phone-bar">
    <div class="phone-icon"><svg width="16" height="16" viewBox="0 0 24 24"><path d="M6.6 10.8a15.1 15.1 0 0 0 6.6 6.6l2.2-2.2a1 1 0 0 1 1-.25 11.4 11.4 0 0 0 3.6.57 1 1 0 0 1 1 1V20a1 1 0 0 1-1 1A17 17 0 0 1 3 4a1 1 0 0 1 1-1h3.5a1 1 0 0 1 1 1c0 1.25.2 2.45.57 3.6a1 1 0 0 1-.25 1z" fill="#fff"/></svg></div>
    <div class="phone-number">555-014-2287</div>
  </div>
</main>
</body>
</html>
```